New Business Card Design Project

Use the flyer uploaded and website www.brightoakbuilders.com for inspiration.
List Our Services on Backside of business cards
Marcus Delling
Harborline Builders Inc.
Licensed General Contractors
858-471-6093

Contact Information for Business Card

Use the flyer uploaded and website www.brightoakbuilders.com for inspiration. List Our Services on Backside of business cards Marcus Delling Harborline Builders Inc. Licensed General Contractors 858-471-6093

```html
<!DOCTYPE html>
<html lang="en">
<head>
<meta charset="utf-8">
<title>Harborline Builders – Business Cards</title>
<link href="https://fonts.googleapis.com/css2?family=Montserrat:wght@400;500;700&display=swap" rel="stylesheet">
<style>
  :root{
    --backdrop:#3b3b3d;
    --card:#1c1c1d;
    --ink:#f2f2f2;
    --ink-soft:#d4d4d4;
    --rule:#8a8a8a;
    --motif-a:#2a2a2b;
    --motif-b:#1c1c1d;
  }
  *{margin:0;padding:0;box-sizing:border-box}
  html,body{width:1200px;height:1200px;overflow:hidden}
  body{
    background:var(--backdrop);
    font-family:"Montserrat",sans-serif;
    color:var(--ink);
    display:flex;flex-direction:column;align-items:center;justify-content:center;gap:56px;
  }
  .card{
    position:relative;width:900px;height:514px;
    background:var(--card);border-radius:30px;
    box-shadow:0 18px 40px rgba(0,0,0,.45);
    overflow:hidden;
  }
  .brand-name{
    position:absolute;z-index:2;white-space:nowrap;
    font-weight:500;letter-spacing:.14em;text-transform:uppercase;color:var(--ink);
  }
  /* services side */
  .services-side .brand-name{left:60px;top:60px;font-size:26px}
  .decor-motif{
    position:absolute;z-index:1;right:50px;top:40px;width:330px;height:430px;border-radius:20px;
    background:radial-gradient(ellipse at 50% 35%,var(--motif-a),var(--motif-b) 70%);
  }
  .services{position:absolute;z-index:2;left:60px;top:140px}
  .services h2{
    font-size:24px;font-weight:700;padding-bottom:8px;
    border-bottom:1px solid var(--rule);display:inline-block;padding-right:30px;margin-bottom:12px;
  }
  .services ul{list-style:none}
  .services li{font-size:18px;line-height:28px;color:var(--ink-soft);padding-left:28px;position:relative}
  .services li::before{content:"";position:absolute;left:4px;top:11px;width:7px;height:7px;border-radius:50%;background:var(--ink)}
  /* contact side */
  .person{position:absolute;left:64px;top:70px}
  .person-name{font-size:40px;font-weight:700}
  .person-role{font-size:20px;color:var(--ink-soft);margin-top:2px}
  .contact-side .brand-name{right:64px;top:205px;font-size:34px;text-align:right}
  .license{position:absolute;left:64px;top:318px;font-size:19px;color:var(--ink-soft)}
  .contacts{position:absolute;left:64px;top:370px;list-style:none}
  .contacts li{display:flex;align-items:center;gap:18px;font-size:19px;line-height:36px;color:var(--ink-soft)}
  .contacts svg{width:20px;height:20px;fill:var(--ink)}
</style>
</head>
<body>
  <section class="card services-side">
    <div class="brand-name">Harborline Builders</div>
    <div class="decor-motif" role="img" aria-label="Faint tonal decorative motif area"></div>
    <div class="services">
      <h2>Our Services</h2>
      <ul>
        <li>Remodel: Kitchen &amp; Bath</li>
        <li>Painting: Interior &amp; Exterior</li>
        <li>Flooring: Carpet, Vinyl, Wood</li>
        <li>Window: Door Replacement</li>
        <li>Plumbing: Repair &amp; Upgrades</li>
        <li>Energy Efficient Upgrades</li>
        <li>Deck &amp; Patio construction</li>
        <li>Water &amp; Mold Damage</li>
        <li>Garage Renovation</li>
      </ul>
    </div>
  </section>

  <section class="card contact-side">
    <div class="person">
      <div class="person-name">Marcus Delling</div>
      <div class="person-role">Managing Director</div>
    </div>
    <div class="brand-name">Harborline Builders</div>
    <div class="license">CSLB Licensed No. #1048265</div>
    <ul class="contacts">
      <li><svg viewBox="0 0 24 24" aria-hidden="true"><path d="M6.6 10.8a15.1 15.1 0 0 0 6.6 6.6l2.2-2.2a1 1 0 0 1 1-.25 11.4 11.4 0 0 0 3.6.57 1 1 0 0 1 1 1V20a1 1 0 0 1-1 1A17 17 0 0 1 3 4a1 1 0 0 1 1-1h3.5a1 1 0 0 1 1 1c0 1.25.2 2.45.57 3.57a1 1 0 0 1-.25 1z"/></svg>858-471-6093</li>
      <li><svg viewBox="0 0 24 24" aria-hidden="true"><path d="M2 5h20v14H2z M2 5l10 8 10-8" fill="none" stroke="#f2f2f2" stroke-width="2"/></svg>info@brightoakbuilders.com</li>
      <li><svg viewBox="0 0 24 24" aria-hidden="true"><circle cx="12" cy="12" r="9" fill="none" stroke="#f2f2f2" stroke-width="2"/><path d="M3 12h18M12 3c3 3 3 15 0 18M12 3c-3 3-3 15 0 18" fill="none" stroke="#f2f2f2" stroke-width="1.5"/></svg>www.brightoakbuilders.com</li>
    </ul>
  </section>
</body>
</html>
```